Banner Pop Up Opt In Form REDESIGNS - SLEEK BLACK LOOK

Please redesign banners attached.

I am looking for a very sleek look....I do not like this collage of images on these current designs. Please keep all content same but use images that pop.

I have an acccount at www.pixvane-example.com or you can use your own images.

I like black background for somereason because it looks very sleek....but these designs should pop , build trust and credibility and have easy opt in form....SLEEK AND MODERN LOOK is what im looking for....

Target Market(s)

Consumers on websites

Requirements
Must have
• Please redesign banners attached.

Nice to have

Should not have

```html
<!DOCTYPE html>
<html lang="en">
<head>
<meta charset="utf-8">
<title>Hotel Savings Card Opt-In Banners</title>
<link rel="stylesheet" href="https://fonts.googleapis.com/css2?family=Questrial&family=Pathway+Gothic+One&display=swap">
<style>
  :root {
    --bg-black: #0c0c0c;
    --bg-leather: #1c1c1c;
    --divider: #3a3a3a;
    --gold-light: #fbe7a1;
    --gold-mid: #d6a93c;
    --gold-dark: #8a6418;
    --green: #5bb318;
    --green-light: #8fd43a;
    --green-dark: #3f7d0e;
    --field: #ffffff;
    --white: #f4f4f4;
  }
  * { margin: 0; padding: 0; box-sizing: border-box; }
  html, body { width: 1200px; height: 516px; overflow: hidden; background: var(--bg-black); }
  .canvas { position: relative; width: 1200px; height: 516px; overflow: hidden; }
  .banner {
    position: absolute; top: 0; width: 600px; height: 516px;
    background: radial-gradient(ellipse at 50% 40%, var(--bg-leather) 0%, var(--bg-black) 75%);
    overflow: hidden;
  }
  .banner--offer { left: 0; }
  .banner--win { left: 600px; border-left: 1px solid var(--divider); }
  .headline {
    position: absolute; left: 0; width: 100%;
    font-family: "Questrial", sans-serif; text-align: center; line-height: 1;
    background: linear-gradient(180deg, var(--gold-light) 0%, var(--gold-mid) 45%, var(--gold-dark) 60%, var(--gold-mid) 80%, var(--gold-light) 100%);
    -webkit-background-clip: text; background-clip: text; color: transparent;
  }
  .headline__line { display: block; }
  .subtitle {
    position: absolute; left: 0; width: 100%; text-align: center;
    font-family: "Pathway Gothic One", sans-serif; font-size: 20px; line-height: 1;
    color: var(--gold-mid); letter-spacing: 0.2px;
  }
  .offer-amount {
    position: absolute; left: 0; width: 100%; text-align: center;
    font-family: "Pathway Gothic One", sans-serif; font-size: 20px; line-height: 1;
    color: var(--green);
  }
  .field {
    position: absolute; display: block; height: 42px;
    background: var(--field);
    border: 3px solid var(--gold-mid);
    box-shadow: inset 0 0 0 1px var(--gold-light);
  }
  .submit {
    position: absolute; height: 33px;
    background: linear-gradient(180deg, var(--green-light) 0%, var(--green) 50%, var(--green-dark) 100%);
    border: 1px solid var(--green-dark); border-radius: 2px;
    font-family: "Pathway Gothic One", sans-serif; font-size: 22px; line-height: 31px;
    color: #0a0a0a; text-align: center;
  }
  .travel-photo {
    position: absolute;
    background: radial-gradient(ellipse at 45% 40%, #a8d832 0%, #7fb51d 40%, #2a3310 75%, rgba(12,12,12,0) 100%);
  }
  .footnote {
    position: absolute; top: 491px;
    font-family: "Questrial", sans-serif; font-size: 10.4px; line-height: 1;
    color: var(--white); white-space: nowrap;
  }
</style>
</head>
<body>
<main class="canvas">

  <section class="banner banner--offer">
    <h1 class="headline" style="top:18px; font-size:82px;">
      <span class="headline__line" style="margin-left:-2px;">WANT A</span>
      <span class="headline__line" style="margin-top:-8px; font-size:80px;">GREAT OFFER?</span>
    </h1>
    <p class="subtitle" style="top:170px;">SUBSCRIBE TO OUR NEWSLETTER AND RECEIVE A COMPLIMENTARY</p>
    <p class="offer-amount" style="top:193px; left:-6px;">$500 HOTEL SAVINGS CARD</p>

    <form class="optin">
      <label class="field" style="left:33px; top:243px; width:267px;" aria-label="Name"></label>
      <label class="field" style="left:33px; top:304px; width:267px;" aria-label="Email"></label>
      <label class="field" style="left:33px; top:363px; width:267px;" aria-label="Phone"></label>
      <div class="submit" style="left:103px; top:421px; width:114px;">SUBMIT</div>
    </form>

    <div class="travel-photo" style="left:380px; top:200px; width:202px; height:294px;"
         role="img" aria-label="Lime green suitcase with a straw hat and two cocktails"></div>

    <p class="footnote" style="left:35px;">WE WILL SEND AN EMAIL AND A TEXT MESAGE WITH THE OFFER AND HOW TO REDEEM</p>
  </section>

  <section class="banner banner--win">
    <h1 class="headline" style="top:30px; font-size:80px;">
      <span class="headline__line">ENTER TO WIN!</span>
    </h1>
    <p class="subtitle" style="top:116px;">SUBSCRIBE TO OUR NEWSLETTER AND RECEIVE A COMPLIMENTARY</p>
    <p class="offer-amount" style="top:139px; left:-4px;">$500 HOTEL SAVINGS CARD</p>

    <form class="optin">
      <label class="field" style="left:32px; top:214px; width:268px;" aria-label="Name"></label>
      <label class="field" style="left:32px; top:276px; width:268px;" aria-label="Email"></label>
      <label class="field" style="left:32px; top:334px; width:268px;" aria-label="Phone"></label>
      <div class="submit" style="left:104px; top:392px; width:112px;">SUBMIT</div>
    </form>

    <div class="travel-photo" style="left:381px; top:172px; width:202px; height:294px;"
         role="img" aria-label="Lime green suitcase with a straw hat and two cocktails"></div>

    <p class="footnote" style="left:35px;">WE WILL SEND AN EMAIL AND A TEXT MESAGE WITH THE OFFER AND HOW TO REDEEM</p>
  </section>

</main>
</body>
</html>
```